Wordpress Site Design for a Horror and Action Movie Production Company

We need a re-design/facelift of our website: https://k42t.pagecraft.io
The structure of the website could remain the same, but it needs to look and feel BETTER!

We would like the website coded in Wordpress so that it can be easily updated bu us, via adding new projects and new projects' info.

We specialize in Action, Horror, and Sci-Fi Genre. That being said, we don't want the website to look like it's a themed park with haunted houses. It should still be sharp and professional, as after all - it is a business for us!

Target Market(s)

Film Distribution Companies (B2B), as well as general audience that likes movies

Industry/Entity Type

Movie Production

Coding

Coded - Design and coding required

Number of Pages Required

5+ page

Font styles to use
Sans Serif

Colors

Designer to choose colors to be used in the design.

Requirements
Must have
• - PROJECTS page
• - Each PROJECT has a sub-page with project info/updates (up dates could be in a form of a WP post, ideally a template that we can use to update and create new PROJECT pages, with text, poster, and video link (trailer))
• - NEWS page that chronologically lists updates from all PROJECTS (could be done via WP blog)
• - HOME page would
Nice to have
• Should generally have a dark background.
• Websites we like as a reference of general approach and style:
• https://marbletoq.com
• https://velunpix.com (however this is very image-centric, and we might not have that much imagery at the moment)
• https://www.copperfieldechoandframe.com/other
• https://quennreels.com
Should not have
• We specialize in Action, Horror, and Sci-Fi Genre. That being said, we don't want the website to look like it's a themed park with haunted houses. It should still be sharp and professional, as after all - it is a business for us!

```html
<!DOCTYPE html>
<html lang="en">
<head>
<meta charset="utf-8">
<title>Kiln 42 Media</title>
<link href="https://fonts.googleapis.com/css2?family=Ubuntu:wght@400;500&family=Nunito+Sans:wght@300;400&display=swap" rel="stylesheet">
<style>
:root{
  --ink:#0f0f12;
  --field:#2a2a2d;
  --orange:#ec7c1b;
  --red:#ff3535;
  --white:#ffffff;
  --grey-text:#bfbfbf;
  --title-dark:#151515;
  --card-text:#3a3a3a;
  --rule:#dcdcdc;
}
*{margin:0;padding:0;box-sizing:border-box}
html,body{width:1200px;height:3427px;overflow:hidden}
body{position:relative;background:var(--white);font-family:"Nunito Sans",sans-serif;color:var(--white)}
.abs{position:absolute}
.dark-top{left:0;top:0;width:1200px;height:1320px;background:var(--ink)}
.hero-still{left:0;top:95px;width:1200px;height:570px;background:radial-gradient(ellipse 420px 300px at 50% 45%,#7a4a2a 0%,#4a2a18 40%,#1e140f 75%,var(--ink) 100%)}
.brand{font-family:"Ubuntu",sans-serif;font-weight:500;color:var(--white);letter-spacing:2px;display:flex;align-items:center;gap:10px}
.brand-mark{width:12px;height:12px;background:var(--orange)}
.header-brand{left:77px;top:42px;font-size:26px}
.nav{right:77px;top:52px;display:flex;gap:27px;font-family:"Nunito Sans",sans-serif;font-size:14px;letter-spacing:.3px}
.nav a{color:var(--white);text-decoration:none;padding-top:8px}
.nav a.current{color:var(--orange);border-top:1px solid var(--orange)}
.profile{left:0;top:712px;width:1200px;text-align:center}
.section-title{font-family:"Ubuntu",sans-serif;font-weight:400;font-size:37px;letter-spacing:.5px}
.profile p{width:640px;margin:0 auto;font-size:15.5px;line-height:27px;color:var(--grey-text);font-weight:300}
.profile .section-title{margin-bottom:28px}
.profile p+p{margin-top:15px}
.outline-btn{display:block;border:1.5px solid var(--white);border-radius:26px;color:var(--orange);font-family:"Ubuntu",sans-serif;font-size:18px;text-align:center;line-height:49px;text-decoration:none}
.explore{left:496px;top:967px;width:208px}
.waves{left:0;top:990px}
.projects-intro{left:0;top:1265px;width:1200px;text-align:center}
.projects-intro p{width:620px;margin:14px auto 0;font-size:15.5px;line-height:27px;font-weight:300}
.project{width:323px}
.project .still{height:229px;position:relative}
.project .play{position:absolute;left:50%;top:50%;width:56px;height:56px;margin:-28px 0 0 -28px}
.project h3{font-family:"Ubuntu",sans-serif;font-weight:400;font-size:19.5px;color:var(--card-text);padding:20px 2px 20px;border-bottom:1.5px solid var(--rule);letter-spacing:.3px}
.partners-title{left:0;top:2375px;width:1200px;text-align:center;color:var(--title-dark)}
.dark-bottom{left:0;top:2520px}
.partner{width:240px;top:2459px;background:var(--white);border-radius:0 0 6px 6px;overflow:hidden}
.partner .portrait{height:270px}
.partner p{font-family:"Ubuntu",sans-serif;font-size:17.5px;color:var(--card-text);text-align:center;line-height:64px;letter-spacing:.3px}
.footer-brand{left:0;top:2895px;width:1200px;justify-content:center;font-size:32px}
.field{background:var(--field);color:#d8d8d8;font-size:13.5px;padding:0 18px;line-height:52px;font-family:"Nunito Sans",sans-serif}
.field.message{line-height:1;padding-top:24px}
.submit{left:516px;top:3228px;width:167px;line-height:50px}
.footer-bar{left:0;top:3365px;width:1200px;height:62px;background:linear-gradient(90deg,var(--red),var(--orange));text-align:center;font-size:13px;line-height:62px;font-weight:300}
</style>
</head>
<body>

<div class="abs dark-top"></div>
<div class="abs hero-still" role="img" aria-label="Film still: a figure levitating in a dim, warm-lit stone chamber"></div>

<div class="abs brand header-brand"><span class="brand-mark"></span>KILN 42 MEDIA</div>
<nav class="abs nav">
  <a class="current" href="#">HOME</a><a href="#">ABOUT</a><a href="#">NEWS</a><a href="#">PROJECTS</a><a href="#">CONTACT</a>
</nav>

<section class="abs profile">
  <h2 class="section-title">COMPANY PROFILE</h2>
  <p>Kiln 42 Media Inc (K42M) is a fresh brand of multi-media Visual Content, aimed at development of original Canadian content as well as servicing of foreign productions here at home, in Ontario, Canada.</p>
  <p>K42M is a child of a partnership between two Canadian companies, which for years have been recognized as key brands in the Canadian media landscape:</p>
</section>
<a class="abs outline-btn explore" href="#">EXPLORE MORE</a>

<svg class="abs waves" width="1200" height="556" viewBox="0 0 1200 556">
  <defs>
    <linearGradient id="heat" x1="0" x2="1" y1="0" y2="0">
      <stop offset="0" stop-color="#ff3535"/><stop offset="0.45" stop-color="#f45a24"/><stop offset="1" stop-color="#ec7f1a"/>
    </linearGradient>
  </defs>
  <path d="M0 88 Q260 180 500 186 L1200 40 L1200 556 L0 556Z" fill="#ec7c1b"/>
  <path d="M0 262 Q300 268 500 186 Q850 40 1200 0 L1200 556 L0 556Z" fill="url(#heat)"/>
</svg>

<section class="abs projects-intro">
  <svg width="54" height="50" viewBox="0 0 54 50" fill="none" stroke="#fff" stroke-width="2.2">
    <rect x="2" y="12" width="50" height="36" rx="3"/>
    <path d="M3 3 H51 V12 H3Z"/>
    <path d="M12 3 L7 12 M22 3 L17 12 M32 3 L27 12 M42 3 L37 12 M51 4 L47 12"/>
    <line x1="2" y1="19" x2="52" y2="19"/>
    <path d="M21 24 L36 32 L21 40Z"/>
  </svg>
  <h2 class="section-title">OUR PROJECTS</h2>
  <p>Below is a list of links to some of the recent projects, produced and/or production serviced by Crowfield Pictures or Sevenfold Lantern Studios:</p>
</section>

<article class="abs project" style="left:77px;top:1635px">
  <div class="still" role="img" aria-label="Film still from Northlight: a woman in a car" style="background:linear-gradient(135deg,#6b6a5c,#3c3c35 60%,#25261f)">
    <svg class="play" viewBox="0 0 56 56"><circle cx="28" cy="28" r="28" fill="#ec7c1b"/><path d="M23 19 L37 28 L23 37Z" fill="#fff"/></svg></div>
  <h3>NORTHLIGHT</h3>
</article>
<article class="abs project" style="left:439px;top:1635px">
  <div class="still" role="img" aria-label="Film still from Deep Current: a submarine surfacing at dusk" style="background:linear-gradient(180deg,#f08a86 0%,#d98a8e 35%,#3d4d7a 60%,#22305a)">
    <svg class="play" viewBox="0 0 56 56"><circle cx="28" cy="28" r="28" fill="#ec7c1b"/><path d="M23 19 L37 28 L23 37Z" fill="#fff"/></svg></div>
  <h3>DEEP CURRENT</h3>
</article>
<article class="abs project" style="left:800px;top:1635px">
  <div class="still" role="img" aria-label="Film still from Rocket Youth: a young rider by steel girders" style="background:linear-gradient(135deg,#3c5566,#2b3a44 55%,#4a3b33)">
    <svg class="play" viewBox="0 0 56 56"><circle cx="28" cy="28" r="28" fill="#ec7c1b"/><path d="M23 19 L37 28 L23 37Z" fill="#fff"/></svg></div>
  <h3>ROCKET YOUTH</h3>
</article>
<article class="abs project" style="left:77px;top:1989px">
  <div class="still" role="img" aria-label="Film still from Gone Too Deep: a dressing room mirror scene" style="background:linear-gradient(135deg,#5a4a40,#3a3230 55%,#6a5a52)">
    <svg class="play" viewBox="0 0 56 56"><circle cx="28" cy="28" r="28" fill="#ec7c1b"/><path d="M23 19 L37 28 L23 37Z" fill="#fff"/></svg></div>
  <h3>GONE TOO DEEP</h3>
</article>
<article class="abs project" style="left:439px;top:1989px">
  <div class="still" role="img" aria-label="Poster for Bail Chasers: an armed heroine amid fire" style="background:radial-gradient(ellipse at 45% 55%,#8a2a12,#4a1208 60%,#2a0a05)"></div>
  <h3>BAIL CHASERS</h3>
</article>
<article class="abs project" style="left:800px;top:1989px">
  <div class="still" role="img" aria-label="Film still from Cracked Road: two silhouettes by a lit window" style="background:linear-gradient(90deg,#141414,#2a2a22 45%,#8a8a55 62%,#1a1a16)">
    <svg class="play" viewBox="0 0 56 56"><circle cx="28" cy="28" r="28" fill="#ec7c1b"/><path d="M23 19 L37 28 L23 37Z" fill="#fff"/></svg></div>
  <h3>CRACKED ROAD</h3>
</article>

<h2 class="abs section-title partners-title">OUR PARTNERS</h2>

<svg class="abs dark-bottom" width="1200" height="845" viewBox="0 0 1200 845">
  <path d="M0 45 Q300 0 600 90 Q900 170 1200 70 L1200 845 L0 845Z" fill="#0f0f12"/>
  <path d="M760 170 Q980 90 1200 62 L1200 150 Q1000 160 840 200Z" fill="#ec7c1b"/>
  <path d="M820 160 L900 140 L900 205 L820 205Z" fill="#ff4a2a"/>
</svg>

<div class="abs partner" style="left:77px"><div class="portrait" role="img" aria-label="Black and white portrait of Adrian Holt" style="background:linear-gradient(160deg,#9a9a9a,#4a4a4a 60%,#222)"></div><p>ADRIAN HOLT</p></div>
<div class="abs partner" style="left:346px"><div class="portrait" role="img" aria-label="Black and white portrait of Pavel Orlin" style="background:linear-gradient(160deg,#7a7a7a,#4a4a4a 60%,#2a2a2a)"></div><p>PAVEL ORLIN</p></div>
<div class="abs partner" style="left:615px"><div class="portrait" role="img" aria-label="Black and white portrait of Jonah Brell" style="background:linear-gradient(160deg,#d0d0d0,#7a7a7a 55%,#3a3a3a)"></div><p>JONAH BRELL</p></div>
<div class="abs partner" style="left:883px"><div class="portrait" role="img" aria-label="Black and white portrait of Marcus Pell" style="background:linear-gradient(160deg,#6a6a6a,#2a2a2a 55%,#111)"></div><p>MARCUS PELL</p></div>

<div class="abs brand footer-brand"><span class="brand-mark"></span>KILN 42 MEDIA</div>

<div class="abs field" style="left:77px;top:3025px;width:333px">Name</div>
<div class="abs field" style="left:434px;top:3025px;width:332px">Email</div>
<div class="abs field" style="left:790px;top:3025px;width:333px">Phone</div>
<div class="abs field message" style="left:77px;top:3100px;width:1046px;height:101px">Message</div>
<a class="abs outline-btn submit" href="#">SUBMIT</a>

<footer class="abs footer-bar">©KILN 42 MEDIA - 2019. All Rights Reserved.</footer>

</body>
</html>
```